Orthobiologic, StemCell, Bone Marrow Aspirate Device Distributor

We need a wordpress fully functioning website design for an innovative ortho-biologic, Bone Marrow Aspirate Device that extracts stem cells for orthopedic regenerative medical professionals. We also offer state of the art training in there office setting with licensed medical staff, a full service support team, and software for tracking patient outcome over time. We are an innovative company that prides itself on gold standard support. We will have other offerings on our website and would like a spot for "future" products. We would like to see designs that look professional, medical, and convey support, security, science, and innovation. We prefer shades of blue and red/orange. I particularly like the following websites that also sell the same device in order of preference:regenacelltherapy.comhttps://aspire-medical.eu/marrow-cellution/https://www.matrixbiosurgical.com/#emerging-solutions-in-healthcareElite2elite.comI have attached a few pictures of the device for reference

Target Market(s)

Orthopedics, Regenerative medicine doctors, Industry representatives, Hospitals

Industry/Entity Type

Medical Equipment

Coding

Coded - Design and coding required

Colors
3176b5
33a6d7
f37022
ec1f27

Requirements
Must have
• It must be able to have videos which I can supply, email, online ordering, and sfax. I have a domain name Coralweavesolutions.com . It must have a FAQ section which you can obtain some information from https://www.tolvenclinical.com/solutions#resources
• The device is manufactured by Dulmor and this is the link to the product page http://www.dulmor.com/quintadraw
• I am currently working on a custom logo and should be able to supply that in short order. I prefer shades of blue and red.
Nice to have
• I would love to have a graphic video as seen here: please see quinta draw vs bone marrow aspirate concentrate.
• https://www.tolvenclinical.com/solutions#competition
• I would pay considerably more to have something similar if it is at all possible
Should not have
• Nothing specific

```html
<!DOCTYPE html>
<html lang="en">
<head>
<meta charset="utf-8">
<title>Coralweave Solutions — Innovative Ortho-Biologic</title>
<link href="https://fonts.googleapis.com/css2?family=Lato:wght@300;400;700&family=Nunito:wght@400;600&display=swap" rel="stylesheet">
<style>
:root{
  --blue:#3176b5;
  --sky:#33a6d7;
  --orange:#f37022;
  --red:#ec1f27;
  --ink:#222;
  --muted:#666;
  --black:#050505;
  --foot:#efefef;
  --white:#fff;
}
*{box-sizing:border-box;margin:0;padding:0}
html,body{width:1200px;height:4633px;overflow:hidden}
body{font-family:"Lato",sans-serif;color:var(--ink);background:var(--white);position:relative}
section,header,footer{position:absolute;left:0;width:1200px}
a{color:inherit;text-decoration:none}

.site-header{top:0;height:94px;background:var(--black)}
.brand{position:absolute;left:148px;top:16px;color:var(--white);font-family:"Nunito",sans-serif}
.brand-name{font-size:46px;line-height:48px;font-weight:400;letter-spacing:-0.5px}
.brand-tag{font-size:13px;letter-spacing:3px;color:var(--white);margin-top:-2px}
.main-nav{position:absolute;left:498px;top:52px;display:flex;gap:32px;font-size:14px;color:var(--white);letter-spacing:.5px}

.hero{top:94px;height:566px;background:radial-gradient(ellipse at 50% 45%,#3b63c9 0%,#1c2f86 38%,#0a1240 70%,#050a22 100%)}
.hero-art{position:absolute;inset:0}
.hero h1{position:absolute;top:196px;width:100%;text-align:center;font-weight:400;font-size:48px;color:var(--white);letter-spacing:.5px}
.hero p{position:absolute;top:260px;width:100%;text-align:center;font-size:25px;font-weight:300;color:var(--white)}
.slide-btn{position:absolute;top:229px;width:56px;height:56px;border-radius:50%;background:rgba(120,120,130,.75)}
.slide-btn.prev{left:106px}.slide-btn.next{left:1067px}
.slide-btn svg{position:absolute;left:16px;top:16px}

.about{top:660px;height:511px}
.about-video{position:absolute;left:176px;top:90px;width:411px;height:272px;background:radial-gradient(circle at 55% 45%,#a9c6e8 0%,#3d6aa8 30%,#0e1d3c 70%,#050914 100%)}
.play{position:absolute;left:182px;top:113px;width:74px;height:74px;border-radius:50%;background:var(--white)}
.about h2{position:absolute;left:624px;top:97px;font-size:36px;font-weight:400;line-height:42px;color:var(--blue)}
.about p{position:absolute;left:626px;top:207px;width:420px;font-size:15px;line-height:27px;color:#555;font-weight:300}
.down-arrow{position:absolute;left:585px;top:420px}

.who{top:1171px;height:457px;background:linear-gradient(90deg,#7fb6e6 0%,#4d96d6 30%,#2f7ec6 60%,#2a6cb3 100%)}
.who-art{position:absolute;left:0;top:0;width:600px;height:457px;background:radial-gradient(ellipse at 45% 45%,rgba(170,215,245,.7) 0%,rgba(90,150,215,.3) 45%,rgba(0,0,0,0) 75%)}
.who h2{position:absolute;left:610px;top:115px;font-size:31px;font-weight:300;color:var(--white)}
.who p{position:absolute;left:610px;top:172px;width:450px;font-size:15px;line-height:22px;color:var(--white)}
.btn-outline{display:inline-block;border:2px solid var(--white);color:var(--white);border-radius:28px;font-size:15px;text-align:center}
.who .btn-outline{position:absolute;left:610px;top:267px;width:163px;height:49px;line-height:45px}

.offer{top:1628px;height:540px}
.offer-left{position:absolute;left:0;top:0;width:606px;height:540px;background:linear-gradient(160deg,#f0662a 0%,#ec3c27 60%,var(--red) 100%);color:var(--white)}
.offer-left h2{position:absolute;left:169px;top:87px;font-size:31px;font-weight:300}
.offer-left p{position:absolute;left:171px;width:380px;font-size:14.5px;line-height:27px;font-weight:300}
.why{position:absolute;left:606px;top:0;width:594px;height:540px}
.why h2{position:absolute;left:40px;top:83px;font-size:31px;font-weight:300;color:var(--blue)}
.why-item{position:absolute;left:46px;width:460px}
.why-item svg{position:absolute;left:0;top:0}
.why-item h3{position:absolute;left:90px;top:0;font-size:18px;font-weight:400;color:#111}
.why-item p{position:absolute;left:90px;top:30px;width:380px;font-size:13px;line-height:21px;color:#555}

.mission{top:2168px;height:523px;background:radial-gradient(ellipse at 20% 40%,#8a8a8a 0%,#3d3d3d 25%,#0d0d0d 55%),#111}
.mission-art{position:absolute;inset:0;background:radial-gradient(ellipse at 85% 50%,rgba(150,150,150,.55) 0%,rgba(40,40,40,.2) 30%,rgba(0,0,0,0) 55%)}
.mission-box{position:absolute;left:264px;top:75px;width:666px;height:366px;background:rgba(49,118,181,.92);color:var(--white);text-align:center}
.mission-box h2{margin-top:64px;font-size:32px;font-weight:300}
.mission-box p{margin:16px auto 0;width:540px;font-size:17px;line-height:27px;font-weight:300}
.mission-box .btn-outline{margin-top:24px;width:163px;height:49px;line-height:45px}

.products{top:2691px;height:592px}
.products h2{position:absolute;top:76px;width:100%;text-align:center;font-size:32px;font-weight:300;color:#222}
.product-card{position:absolute;top:149px;width:279px;height:362px;border:2px solid #ddd;background:var(--white);text-align:center}
.product-photo{width:180px;height:150px;margin:20px auto 0}
.product-card h3{margin-top:26px;font-size:17px;font-weight:400;color:#111}
.product-card p{margin:10px auto 0;width:220px;font-size:12.5px;line-height:21px;color:#555}
.btn-red{display:inline-block;margin-top:16px;width:140px;height:40px;line-height:36px;border:2px solid var(--red);color:var(--red);border-radius:22px;font-size:13px}

.faq{top:3283px;height:581px;background:linear-gradient(90deg,#f06225 0%,#ee4626 50%,var(--red) 100%);color:var(--white)}
.faq h2{position:absolute;top:60px;width:100%;text-align:center;font-size:34px;font-weight:300}
.faq-item{position:absolute;left:221px;width:765px;border:1px solid rgba(255,255,255,.7)}
.faq-q{position:absolute;left:24px;top:18px;width:640px;font-size:13.5px;line-height:21px;font-weight:700;text-transform:uppercase}
.faq-a{position:absolute;left:24px;top:70px;width:720px;font-size:13.5px;line-height:18px}
.faq-toggle{position:absolute;right:16px;top:20px;font-size:24px;line-height:24px}

.explore{top:3864px;height:396px}
.explore-circle{position:absolute;top:40px;width:324px;height:324px;border-radius:50%;color:var(--white);text-align:center}
.explore-circle h3{margin-top:122px;font-size:28px;font-weight:300;letter-spacing:.5px}
.explore-circle .rule{width:44px;height:2px;background:var(--white);margin:8px auto 0}
.explore-circle .btn-outline{margin-top:14px;width:138px;height:42px;line-height:38px;font-size:12px}
.c-dist{left:142px;background:radial-gradient(circle at 50% 40%,#465a78 0%,#1a2436 45%,#05080f 80%)}
.c-faq{left:444px;background:radial-gradient(circle at 50% 45%,#2f6ec0 0%,#1c58a8 50%,#0f3f86 100%)}
.c-res{left:746px;background:radial-gradient(circle at 50% 45%,#3a6497 0%,#182c4d 45%,#060b16 80%)}

.site-footer{top:4260px;height:373px;background:var(--foot)}
.foot-col{position:absolute;top:57px}
.foot-col h4{font-size:15px;font-weight:700;color:#222;letter-spacing:.3px}
.foot-col ul{list-style:none;margin-top:18px}
.foot-col li{font-size:13.5px;line-height:27px;color:#444}
.contact-line{position:relative;padding-left:28px;font-size:13.5px;line-height:17px;color:#444;margin-top:0}
.contact-line svg{position:absolute;left:0;top:1px}
.social li{position:relative;padding-left:38px;line-height:34px}
.social li::before{content:"";position:absolute;left:4px;top:7px;width:22px;height:22px;border-radius:50%;background:var(--blue)}
.foot-rule{position:absolute;left:0;top:300px;width:1200px;height:1px;background:#d6d6d6}
.copyright{position:absolute;top:330px;width:100%;text-align:center;font-size:13px;color:#999}
</style>
</head>
<body>

<header class="site-header">
  <div class="brand">
    <div class="brand-name">Coralweave</div>
    <div class="brand-tag">SOLUTIONS | INNOVATIONS FOR LIFE</div>
  </div>
  <nav class="main-nav">
    <a href="#">ABOUT</a><a href="#">PRODUCTS</a><a href="#">SERVICES</a><a href="#">SOLUTION</a><a href="#">NEWS</a><a href="#">CONTACT</a>
  </nav>
</header>

<section class="hero">
  <div class="hero-art" role="img" aria-label="Glowing blue x-ray of a human rib cage and spine over a circuit-line background"></div>
  <h1>INNOVATIVE ORTHO-BIOLOGIC</h1>
  <p>EXTRACTS STEM CELLS FOR ORTHOPEDIC REGENERATIVE</p>
  <a class="slide-btn prev" href="#" aria-label="Previous slide"><svg width="24" height="24" viewBox="0 0 24 24"><path d="M15 4 7 12l8 8" fill="none" stroke="#111" stroke-width="2.5"/></svg></a>
  <a class="slide-btn next" href="#" aria-label="Next slide"><svg width="24" height="24" viewBox="0 0 24 24"><path d="M9 4l8 8-8 8" fill="none" stroke="#111" stroke-width="2.5"/></svg></a>
</section>

<section class="about">
  <div class="about-video" role="img" aria-label="Video still of a blue stem cell under magnification">
    <span class="play"><svg width="74" height="74" viewBox="0 0 74 74"><path d="M29 22v30l24-15z" fill="#111"/></svg></span>
  </div>
  <h2>ABOUT CORALWEAVE<br>SOLUTIONS</h2>
  <p>Coralweave Solutions is a provider of quality, innovative regenerative medicine and ortho-biologic devices coupled with best in class clinical training. We have diverse experience in regenerative solutions as well as exceptional clinical expertise.</p>
  <svg class="down-arrow" width="38" height="50" viewBox="0 0 38 50"><path d="M19 2v44M5 32l14 14 14-14" fill="none" stroke="#3176b5" stroke-width="3"/></svg>
</section>

<section class="who">
  <div class="who-art" role="img" aria-label="Blue-toned illustration of a human pelvis and lower spine"></div>
  <h2>WHO WE ARE</h2>
  <p>Providers of Innovative Ortho Biologic devices staffed with clinical professionals who bring exciting new biologic options to busy practitioners, hospitals, and surgical centers.</p>
  <a class="btn-outline" href="#">CLICK HERE</a>
</section>

<section class="offer">
  <div class="offer-left">
    <h2>WHAT WE OFFER</h2>
    <p style="top:146px">Gold standard client support with effective and efficient treatment solutions for physicians and their patients as well as on-site, personalized, hands-on training with our licensed clinical specialists.</p>
    <p style="top:282px">Our expertise in the clinical use of these technologies and our ability to give hands on training sets the gold standard in our industry. We are driven by a commitment to improve patient outcomes, reduce provider expenses with cost effective products</p>
  </div>
  <div class="why">
    <h2>WHY WE ARE</h2>
    <div class="why-item" style="top:152px">
      <svg width="64" height="70" viewBox="0 0 64 70"><circle cx="32" cy="30" r="24" fill="none" stroke="#f37022" stroke-width="2.5"/><path d="M24 54v8h16v-8" fill="none" stroke="#f37022" stroke-width="2.5"/><circle cx="32" cy="30" r="9" fill="none" stroke="#f37022" stroke-width="2.5"/></svg>
      <h3>INNOVATIVE</h3>
      <p>Vivamus porttitor purus nisi eleifend libero a tempus libero lectus feugiat felis Morbi diam mauris viverra in</p>
    </div>
    <div class="why-item" style="top:272px">
      <svg width="64" height="64" viewBox="0 0 64 64"><circle cx="32" cy="32" r="28" fill="none" stroke="#f37022" stroke-width="2.5"/><circle cx="32" cy="34" r="16" fill="none" stroke="#f37022" stroke-width="2.5"/><path d="M32 34l9-10" stroke="#f37022" stroke-width="2.5"/></svg>
      <h3>EFFICIENT</h3>
      <p>Vivamus porttitor purus nisi eleifend libero a tempus libero lectus feugiat felis Morbi diam mauris</p>
    </div>
    <div class="why-item" style="top:388px">
      <svg width="64" height="66" viewBox="0 0 64 66"><circle cx="34" cy="28" r="24" fill="none" stroke="#f37022" stroke-width="2.5"/><circle cx="34" cy="24" r="6" fill="none" stroke="#f37022" stroke-width="2.5"/><path d="M16 44 4 60" stroke="#f37022" stroke-width="2.5"/></svg>
      <h3>SPECIFIC</h3>
      <p>Vivamus porttitor purus nisi eleifend libero a tempus libero lectus feugiat felis Morbi diam mauris</p>
    </div>
  </div>
</section>

<section class="mission">
  <div class="mission-art" role="img" aria-label="Black and white x-ray of hip joints"></div>
  <div class="mission-box">
    <h2>OUR MISSION</h2>
    <p>To provide medical professionals with the training and tools they need to offer regenerative medical therapies that will become the gold standard of care for the treatment of multiple ortho degenerative diseases and ortho biologic conditions.</p>
    <a class="btn-outline" href="#">CLICK HERE</a>
  </div>
</section>

<section class="products">
  <h2>OUR PRODUCTS</h2>
  <div class="product-card" style="left:160px">
    <div class="product-photo" role="img" aria-label="Purple handled aspiration needle device" style="background:radial-gradient(ellipse at 60% 40%,#6a3fb0 0%,#4b2a8a 25%,#fff 55%)"></div>
    <h3>PRODUCT TITLE</h3>
    <p>Sed ut perspiciatis unde omnis iste natus error sit voluptatem</p>
    <a class="btn-red" href="#">CLICK HERE</a>
  </div>
  <div class="product-card" style="left:457px">
    <div class="product-photo" role="img" aria-label="Blue plunger aspiration device with spring" style="background:radial-gradient(ellipse at 50% 50%,#3040b8 0%,#26309a 22%,#fff 55%)"></div>
    <h3>PRODUCT TITLE</h3>
    <p>Sed ut perspiciatis unde omnis iste natus error sit voluptatem</p>
    <a class="btn-red" href="#">CLICK HERE</a>
  </div>
  <div class="product-card" style="left:752px">
    <div class="product-photo" role="img" aria-label="Silver metal cannula component" style="background:radial-gradient(ellipse at 50% 50%,#b5b5b5 0%,#8c8c8c 25%,#fff 58%)"></div>
    <h3>PRODUCT TITLE</h3>
    <p>Sed ut perspiciatis unde omnis iste natus error sit voluptatem</p>
    <a class="btn-red" href="#">CLICK HERE</a>
  </div>
</section>

<section class="faq">
  <h2>FAQ</h2>
  <div class="faq-item" style="top:113px;height:133px">
    <div class="faq-q">Does a small volume aspirate have more CFU-F than a larger draw that is then volume reduced by centrifugation?</div>
    <div class="faq-toggle">–</div>
    <div class="faq-a">Pellentesque faucibus Ut accumsan ultricies elit Maecenas at justo id velit placerat molestie Donec dictum lectus non odio Cras a ante vitae enim iaculis aliquam Mauris nunc quam venenatis nec</div>
  </div>
  <div class="faq-item" style="top:261px;height:73px">
    <div class="faq-q">What are the limitations of traditional needles and what is the optimal technique for minimizaing peripheral blood dilution?</div>
    <div class="faq-toggle">+</div>
  </div>
  <div class="faq-item" style="top:348px;height:73px">
    <div class="faq-q">Do I need to filter spicules from marrow after aspiration and are red cells a problem?</div>
    <div class="faq-toggle">+</div>
  </div>
  <div class="faq-item" style="top:431px;height:73px">
    <div class="faq-q">Is there a relationship between differing volumes of bone marrow aspirates and their cellular composition?</div>
    <div class="faq-toggle">+</div>
  </div>
</section>

<section class="explore">
  <div class="explore-circle c-dist" role="img" aria-label="Dark blue x-ray of a rib cage">
    <h3>DISTRIBUTORS</h3><div class="rule"></div><a class="btn-outline" href="#">CLICK HERE</a>
  </div>
  <div class="explore-circle c-res" role="img" aria-label="Dark blue x-ray of a pelvis">
    <h3>RESOURCES</h3><div class="rule"></div><a class="btn-outline" href="#">CLICK HERE</a>
  </div>
  <div class="explore-circle c-faq" role="img" aria-label="Blue-toned photo of medical equipment">
    <h3>FAQ</h3><div class="rule"></div><a class="btn-outline" href="#">CLICK HERE</a>
  </div>
</section>

<footer class="site-footer">
  <div class="foot-col" style="left:169px">
    <h4>CONTACT US</h4>
    <div style="margin-top:24px">
      <p class="contact-line"><svg width="16" height="18" viewBox="0 0 16 18"><path d="M8 17s6-6 6-10A6 6 0 0 0 2 7c0 4 6 10 6 10z" fill="none" stroke="#333" stroke-width="1.6"/><circle cx="8" cy="7" r="2" fill="#333"/></svg>48 Harlow Avenue #3B<br>Austin 78702 TX</p>
      <p class="contact-line" style="margin-top:18px"><svg width="16" height="16" viewBox="0 0 16 16"><path d="M3 1h3l1.5 4-2 1.5a9 9 0 0 0 4 4l1.5-2 4 1.5v3a1.5 1.5 0 0 1-1.5 1.5A13 13 0 0 1 1.5 2.5 1.5 1.5 0 0 1 3 1z" fill="none" stroke="#333" stroke-width="1.4"/></svg>555.214.7730</p>
      <p class="contact-line" style="margin-top:18px"><svg width="16" height="14" viewBox="0 0 16 14"><rect x="1" y="2" width="14" height="10" fill="none" stroke="#333" stroke-width="1.4"/><path d="M1 2l7 6 7-6" fill="none" stroke="#333" stroke-width="1.4"/></svg>hello@coralweavesolutions.com</p>
    </div>
  </div>
  <div class="foot-col" style="left:426px">
    <h4>COMPANY</h4>
    <ul><li>Home</li><li>About us</li><li>Services</li><li>Products</li><li>Contact</li></ul>
  </div>
  <div class="foot-col" style="left:570px">
    <h4>PRODUCTS</h4>
    <ul><li>Sed porta</li><li>Suspendisse quam</li><li>Leo molestie</li><li>Sed luctus</li><li>Fermentum</li></ul>
  </div>
  <div class="foot-col" style="left:750px">
    <h4>RESOURCES</h4>
    <ul><li>FAQ</li><li>Videos</li><li>News</li><li>Contact Us</li></ul>
  </div>
  <div class="foot-col" style="left:914px">
    <h4>GET IN TOUCH</h4>
    <ul class="social" style="margin-top:10px"><li>Pulsewire</li><li>Hearthub</li><li>Proflink</li><li>Lenscape</li></ul>
  </div>
  <div class="foot-rule"></div>
  <p class="copyright">Copyright © 2019 All right reserved</p>
</footer>

</body>
</html>
```